Design a web site for my business - Brightline Coatings Co.

We are a family business that handles design, fabrication and installation of powder coated aluminum, stainless steel and glass products. Including handrails, privacy slat screens, electric gates and pool fencing. We are based in the Whitsundays in North Queensland and service an area from Airlie Beach to Townsville.

Target Market(s)

Domestic and commercial

Industry/Entity Type

fabrication - manufacturing

Coding

Coded - Design and coding required

Number of Pages Required

5+ page

Colors
0054AA
0677BA
7BADD7
CADEEF
E8F1F8

Requirements
Must have
• photo galleries, contact page, one page for privacy screens, balustrades, glass fencing, stainless steel handrail, powder coated aluminium handrails and pool fencing

```html
<!DOCTYPE html>
<html lang="en">
<head>
<meta charset="utf-8">
<title>Brightline Coatings Co</title>
<link rel="stylesheet" href="https://fonts.googleapis.com/css2?family=Figtree:wght@400;500;600;700&display=swap">
<style>
:root{
  --stage:#0a1628;
  --navy:#0b1f38;
  --navy-2:#10284a;
  --gold:#a7781f;
  --ink:#14213a;
  --body:#3a4658;
  --line:#e3e6eb;
  --sand:#f4f2ee;
  --white:#ffffff;
  --sky:#7badd7;
  --sea:#0677ba;
}
*{box-sizing:border-box;margin:0;padding:0}
html,body{width:1200px;height:2219px;overflow:hidden;background:var(--stage);font-family:"Figtree",sans-serif;color:var(--ink)}
.page{position:absolute;left:110px;top:76px;width:979px;height:2065px;background:var(--white);overflow:hidden}
.abs{position:absolute}
svg{display:block}
.ico{fill:none;stroke:var(--ink);stroke-width:1.6;stroke-linecap:round;stroke-linejoin:round}

/* header */
.site-header{left:0;top:0;width:979px;height:92px;background:var(--white)}
.brand{left:34px;top:0;width:244px;height:93px;background:var(--white);box-shadow:0 4px 10px rgba(0,0,0,.15);z-index:3;display:flex;align-items:center;gap:10px;padding-left:16px}
.brand-mark{width:22px;height:22px;background:var(--navy)}
.brand-name{font-weight:700;font-size:19px;line-height:1.05;color:var(--navy);letter-spacing:.3px;text-transform:uppercase}
.nav{left:325px;top:38px;display:flex;gap:24px;font-size:13px;color:var(--ink)}
.nav .active{border-bottom:2px solid var(--navy);padding-bottom:8px;font-weight:500}
.call-btn{left:843px;top:31px;width:111px;height:36px;background:var(--navy);border-radius:4px;color:var(--white);font-size:11px;font-weight:600;display:flex;align-items:center;justify-content:center;gap:7px}

/* hero */
.hero{left:0;top:92px;width:979px;height:618px;background:linear-gradient(180deg,#bcd9ef 0%,#8fc0e2 35%,#3f8fc2 55%,#2f7cab 68%,#5f8f4a 82%,#3f6b2e 100%)}
.hero-build{left:540px;top:92px;width:439px;height:618px;background:linear-gradient(160deg,#3b4652 0%,#26303b 40%,#6f7f8c 75%,#c9d2d8 100%);opacity:.88}
.hero-fade{left:0;top:92px;width:620px;height:618px;background:linear-gradient(90deg,rgba(255,255,255,.55),rgba(255,255,255,0))}
.eyebrow{font-size:12px;font-weight:700;letter-spacing:1.2px;color:var(--gold);text-transform:uppercase}
.hero-eyebrow{left:60px;top:197px}
.hero-title{left:60px;top:228px;font-size:50px;line-height:55px;font-weight:700;color:var(--navy);letter-spacing:-.5px}
.hero-copy{left:60px;top:413px;width:330px;font-size:15px;line-height:26px;color:var(--ink)}
.btn{height:42px;border-radius:3px;font-size:11px;font-weight:700;letter-spacing:.8px;display:flex;align-items:center;justify-content:center;gap:10px;text-transform:uppercase}
.btn-dark{background:var(--navy);color:var(--white)}
.btn-line{border:1.5px solid var(--navy);color:var(--navy);background:rgba(255,255,255,.35)}

/* features */
.features{left:49px;top:655px;width:882px;height:215px;background:var(--white);border-radius:8px;box-shadow:0 6px 22px rgba(10,22,40,.12);display:flex;padding:30px 0}
.feature{flex:1;text-align:center;border-right:1px solid var(--line);padding:0 12px}
.feature:last-child{border-right:0}
.feature svg{margin:0 auto 16px}
.feature h3{font-size:12px;font-weight:700;letter-spacing:.5px;line-height:18px;text-transform:uppercase;margin-bottom:10px}
.feature p{font-size:11px;line-height:20px;color:var(--body)}

/* about */
.about-eyebrow{left:50px;top:930px}
.about-title{left:50px;top:963px;font-size:32px;line-height:40px;font-weight:700;color:var(--navy);letter-spacing:-.3px}
.about-copy{left:50px;top:1061px;width:305px;font-size:12px;line-height:22.5px;color:var(--body)}
.about-copy p+p{margin-top:13px}
.tile{border-radius:5px;overflow:hidden}
.tile-label{position:absolute;left:18px;bottom:18px;color:var(--white);font-size:12px;font-weight:600;letter-spacing:.8px;display:flex;align-items:center;gap:10px;text-transform:uppercase}
.tile-shade{position:absolute;inset:0;background:linear-gradient(180deg,rgba(0,0,0,0) 55%,rgba(0,0,0,.55))}

/* climate */
.climate{left:49px;top:1362px;width:882px;height:154px;background:var(--sand);border-radius:6px}
.climate-art{left:34px;top:33px;width:100px;height:90px;border-radius:6px;background:linear-gradient(180deg,#e9edf2,#c9d9e8)}
.climate-head{left:166px;top:37px;font-size:12px;font-weight:700;letter-spacing:.6px;line-height:20px;text-transform:uppercase}
.climate-copy{left:166px;top:90px;width:200px;font-size:10px;line-height:20px;color:var(--body)}
.climate-div{left:398px;top:22px;width:1px;height:110px;background:#d6d3cc}
.trait{top:32px;width:110px;text-align:center;font-size:12px;font-weight:600;line-height:19px}
.trait svg{margin:0 auto 10px}

/* cta */
.cta{left:49px;top:1555px;width:882px;height:120px;background:var(--navy);border-radius:8px;color:var(--white)}
.cta-small{left:79px;top:37px;font-size:9px;font-weight:600;letter-spacing:.8px;text-transform:uppercase}
.cta-big{left:79px;top:56px;font-size:22px;font-weight:500}
.cta-div{left:390px;top:34px;width:1px;height:46px;background:rgba(255,255,255,.35)}
.cta-text{left:435px;top:51px;font-size:14px}
.cta-btn{left:681px;top:37px;width:166px;height:41px;border:1.5px solid rgba(255,255,255,.7);color:var(--white);font-size:10px}

/* footer */
.site-footer{left:0;top:1709px;width:979px;height:356px;background:var(--navy);color:var(--white)}
.foot-brand{left:48px;top:44px;display:flex;align-items:center;gap:9px}
.foot-brand .brand-mark{background:var(--white);width:18px;height:18px}
.foot-brand .brand-name{color:var(--white);font-size:16px}
.foot-about{left:48px;top:108px;width:200px;font-size:11px;line-height:22px;color:#d5dce6}
.socials{left:48px;top:205px;display:flex;gap:13px}
.socials span{width:30px;height:30px;border:1.5px solid #cfd7e2;border-radius:50%}
.foot-col{top:44px;font-size:11px;color:#d5dce6}
.foot-col h4{font-size:11px;font-weight:700;letter-spacing:1px;color:var(--white);margin-bottom:16px;text-transform:uppercase}
.foot-col li{list-style:none;height:29.7px;display:flex;align-items:center;gap:8px}
.foot-vdiv{top:40px;width:1px;height:215px;background:rgba(255,255,255,.15)}
.contact li{height:auto;align-items:flex-start;gap:12px;margin-bottom:17px;line-height:19px}
.contact svg{stroke:var(--white)}
.foot-rule{left:48px;top:288px;width:883px;height:1px;background:rgba(255,255,255,.2)}
.copyright{left:48px;top:316px;font-size:10px;color:#d5dce6}
.legal{left:644px;top:316px;font-size:10px;color:#d5dce6;display:flex;gap:14px}
.legal i{width:1px;height:12px;background:rgba(255,255,255,.4)}
.to-top{left:885px;top:303px;width:36px;height:37px;border:1px solid rgba(255,255,255,.5);border-radius:3px;display:flex;align-items:center;justify-content:center}
</style>
</head>
<body>
<div class="page">

  <header class="site-header abs">
    <div class="brand abs"><span class="brand-mark"></span><span class="brand-name">Brightline<br>Coatings Co</span></div>
    <nav class="nav abs">
      <span class="active">Home</span><span>About Us</span><span>Products &amp; Services ⌄</span><span>Our Work</span><span>Process</span><span>Contact Us</span>
    </nav>
    <div class="call-btn abs">
      <svg width="12" height="12" viewBox="0 0 24 24"><path d="M6.6 10.8a15 15 0 0 0 6.6 6.6l2.2-2.2a1 1 0 0 1 1-.25 11 11 0 0 0 3.6.6 1 1 0 0 1 1 1V20a1 1 0 0 1-1 1A17 17 0 0 1 3 4a1 1 0 0 1 1-1h3.5a1 1 0 0 1 1 1 11 11 0 0 0 .6 3.6 1 1 0 0 1-.25 1z" fill="#fff"/></svg>
      07 5550 1432
    </div>
  </header>

  <section class="hero abs" role="img" aria-label="Photo of a modern coastal home with glass balustrade and black slat screens overlooking a tropical bay and pool"></section>
  <div class="hero-build abs" role="img" aria-label="Modern house with timber ceiling, black slat screening and frameless glass balustrade"></div>
  <div class="hero-fade abs"></div>
  <p class="eyebrow hero-eyebrow abs">Design. Fabrication. Installation.</p>
  <h1 class="hero-title abs">Quality Aluminium,<br>Stainless Steel &amp;<br>Glass Solutions</h1>
  <p class="hero-copy abs">Proudly servicing the Whitsundays and surrounding areas from Airlie Beach to Townsville with premium, custom-made solutions.</p>
  <a class="btn btn-dark abs" style="left:60px;top:521px;width:158px">Our Services
    <svg width="14" height="10" viewBox="0 0 14 10"><path d="M1 5h11M8 1l4 4-4 4" stroke="#fff" stroke-width="1.5" fill="none"/></svg></a>
  <a class="btn btn-line abs" style="left:237px;top:521px;width:147px">View Our Work</a>

  <section class="features abs">
    <div class="feature">
      <svg class="ico" width="40" height="40" viewBox="0 0 40 40"><circle cx="15" cy="13" r="6"/><path d="M4 33c0-7 5-11 11-11s11 4 11 11"/><circle cx="27" cy="12" r="5"/><path d="M28 21c5 0 9 4 9 10"/></svg>
      <h3>Family Owned<br>&amp; Operated</h3><p>Personal service with<br>a local touch.</p>
    </div>
    <div class="feature">
      <svg class="ico" width="40" height="40" viewBox="0 0 40 40"><path d="M20 4l13 5v10c0 9-6 15-13 18C13 34 7 28 7 19V9z"/><path d="M14 20l4 4 8-8"/></svg>
      <h3>Premium<br>Quality</h3><p>Built to last with superior<br>materials &amp; finishes.</p>
    </div>
    <div class="feature">
      <svg class="ico" width="40" height="40" viewBox="0 0 40 40"><path d="M6 34L26 14M24 8l8 8 4-4-8-8zM8 6l6 6-3 3-6-6zM22 24l10 10 3-3-10-10"/></svg>
      <h3>Design to<br>Installation</h3><p>End-to-end service<br>you can trust.</p>
    </div>
    <div class="feature">
      <svg class="ico" width="40" height="40" viewBox="0 0 40 40"><path d="M5 18L20 5l15 13M9 15v20h22V15M15 35V23h10v12M18 23v12M22 23v12"/></svg>
      <h3>Custom<br>Solutions</h3><p>Tailored to suit your<br>space and lifestyle.</p>
    </div>
    <div class="feature">
      <svg class="ico" width="40" height="40" viewBox="0 0 40 40"><path d="M20 37s12-12 12-21a12 12 0 0 0-24 0c0 9 12 21 12 21z"/><circle cx="20" cy="16" r="4"/></svg>
      <h3>Local Experts</h3><p>Based in the Whitsundays,<br>servicing from Airlie Beach<br>to Townsville.</p>
    </div>
  </section>

  <p class="eyebrow about-eyebrow abs" style="font-size:11px">About Us</p>
  <h2 class="about-title abs">Local Craftsmanship.<br>Exceptional Results.</h2>
  <div class="about-copy abs">
    <p>With years of experience in the Whitsundays, we take pride in delivering high-quality aluminium, stainless steel and glass products that combine style, strength and functionality.</p>
    <p>From modern homes to commercial projects, we work closely with our clients to bring their vision to life—on time and to the highest standard.</p>
  </div>
  <a class="btn btn-dark abs" style="left:50px;top:1260px;width:185px;font-size:10px">Learn More About Us
    <svg width="14" height="10" viewBox="0 0 14 10"><path d="M1 5h11M8 1l4 4-4 4" stroke="#fff" stroke-width="1.5" fill="none"/></svg></a>

  <div class="tile abs" style="left:386px;top:908px;width:279px;height:202px;background:linear-gradient(180deg,#8ec0e6 0%,#3d86bf 45%,#5d7b52 80%,#3a4a3a 100%)" role="img" aria-label="Glass balustrade on a terrace overlooking the ocean">
    <div class="tile-shade"></div><span class="tile-label">Handrails <svg width="13" height="10" viewBox="0 0 14 10"><path d="M1 5h11M8 1l4 4-4 4" stroke="#fff" stroke-width="1.5" fill="none"/></svg></span></div>
  <div class="tile abs" style="left:668px;top:908px;width:261px;height:202px;background:linear-gradient(120deg,#9fc4e0 0%,#4a3a2c 30%,#2c2119 70%,#5a4d40 100%)" role="img" aria-label="Timber-look privacy slat screen">
    <div class="tile-shade"></div><span class="tile-label">Privacy Slat Screens <svg width="13" height="10" viewBox="0 0 14 10"><path d="M1 5h11M8 1l4 4-4 4" stroke="#fff" stroke-width="1.5" fill="none"/></svg></span></div>
  <div class="tile abs" style="left:386px;top:1115px;width:279px;height:211px;background:linear-gradient(180deg,#7fb3dd 0%,#c7ccd0 35%,#2b2f35 60%,#3c4046 100%)" role="img" aria-label="Black horizontal slat electric gate at a modern home">
    <div class="tile-shade"></div><span class="tile-label">Electric Gates <svg width="13" height="10" viewBox="0 0 14 10"><path d="M1 5h11M8 1l4 4-4 4" stroke="#fff" stroke-width="1.5" fill="none"/></svg></span></div>
  <div class="tile abs" style="left:668px;top:1115px;width:261px;height:211px;background:linear-gradient(180deg,#6f9d5e 0%,#9fb6a8 35%,#5fb6c8 60%,#7f8f72 100%)" role="img" aria-label="Frameless glass pool fencing around a backyard pool">
    <div class="tile-shade"></div><span class="tile-label">Pool Fencing <svg width="13" height="10" viewBox="0 0 14 10"><path d="M1 5h11M8 1l4 4-4 4" stroke="#fff" stroke-width="1.5" fill="none"/></svg></span></div>

  <section class="climate abs">
    <div class="climate-art abs" role="img" aria-label="Line illustration of sun, palm tree island and waves"></div>
    <p class="climate-head abs">Built for<br>North Queensland</p>
    <p class="climate-copy abs">Our products are designed to withstand the tropical climate and coastal conditions.</p>
    <div class="climate-div abs"></div>
    <div class="trait abs" style="left:424px">
      <svg class="ico" width="40" height="40" viewBox="0 0 40 40"><circle cx="20" cy="20" r="17"/><path d="M8 8l24 24M14 25c3-1 5-4 6-8 2 3 4 5 7 6"/></svg>Corrosion<br>Resistant</div>
    <div class="trait abs" style="left:561px">
      <svg class="ico" width="40" height="40" viewBox="0 0 40 40"><circle cx="20" cy="20" r="7"/><path d="M20 4v6M20 30v6M4 20h6M30 20h6M9 9l4 4M27 27l4 4M9 31l4-4M27 13l4-4"/></svg>UV<br>Protection</div>
    <div class="trait abs" style="left:699px">
      <svg class="ico" width="40" height="40" viewBox="0 0 40 40"><path d="M20 4l13 5v10c0 9-6 15-13 18C13 34 7 28 7 19V9z"/><path d="M14 20l4 4 8-8"/></svg>Built to Last</div>
  </section>

  <section class="cta abs">
    <svg class="abs" style="left:36px;top:34px" width="28" height="44" viewBox="0 0 28 44"><path d="M14 42S26 26 26 14a12 12 0 0 0-24 0c0 12 12 28 12 28z" fill="none" stroke="#fff" stroke-width="1.6"/><circle cx="14" cy="14" r="4" fill="none" stroke="#fff" stroke-width="1.6"/></svg>
    <p class="cta-small abs">Servicing the Whitsundays</p>
    <p class="cta-big abs">Airlie Beach to Townsville</p>
    <div class="cta-div abs"></div>
    <p class="cta-text abs">Let's bring your next project to life.</p>
    <a class="btn cta-btn abs">Get a Free Quote
      <svg width="14" height="10" viewBox="0 0 14 10"><path d="M1 5h11M8 1l4 4-4 4" stroke="#fff" stroke-width="1.5" fill="none"/></svg></a>
  </section>

  <footer class="site-footer abs">
    <div class="foot-brand abs"><span class="brand-mark"></span><span class="brand-name">Brightline<br>Coatings Co</span></div>
    <p class="foot-about abs">Design, fabrication and installation of premium aluminium, stainless steel and glass products. Proudly family owned and operated in the Whitsundays.</p>
    <div class="socials abs" aria-label="Social links"><span></span><span></span><span></span></div>

    <div class="foot-vdiv abs" style="left:266px"></div>
    <div class="foot-col abs" style="left:304px">
      <h4>Quick Links</h4>
      <ul><li>Home</li><li>About Us</li><li>Products &amp; Services <svg width="13" height="10" viewBox="0 0 14 10"><path d="M1 5h11M8 1l4 4-4 4" stroke="#fff" stroke-width="1.4" fill="none"/></svg></li><li>Our Work</li><li>Process</li><li>Contact Us</li></ul>
    </div>
    <div class="foot-vdiv abs" style="left:458px"></div>
    <div class="foot-col abs" style="left:502px">
      <h4>Our Services</h4>
      <ul><li>Handrails</li><li>Privacy Slat Screens</li><li>Electric Gates</li><li>Pool Fencing</li><li>Glass Solutions</li><li>Custom Fabrication</li></ul>
    </div>
    <div class="foot-vdiv abs" style="left:661px"></div>
    <div class="foot-col contact abs" style="left:697px">
      <h4>Contact Us</h4>
      <ul>
        <li><svg class="ico" width="20" height="20" viewBox="0 0 24 24"><path d="M6.6 10.8a15 15 0 0 0 6.6 6.6l2.2-2.2 4.6 1.2V20A17 17 0 0 1 3 4h3.6l1.2 4.6z"/></svg>07 5550 1432</li>
        <li><svg class="ico" width="20" height="20" viewBox="0 0 24 24"><rect x="2" y="5" width="20" height="14"/><path d="M2 6l10 7 10-7"/></svg>hello@brightlinecoatings.example</li>
        <li><svg class="ico" width="20" height="20" viewBox="0 0 24 24"><path d="M12 22s7-7 7-13a7 7 0 0 0-14 0c0 6 7 13 7 13z"/><circle cx="12" cy="9" r="2.5"/></svg>Unit 4, 18 Foundry Court,<br>Cannonvale QLD 4802</li>
        <li><svg class="ico" width="20" height="20" viewBox="0 0 24 24"><circle cx="12" cy="12" r="10"/><path d="M12 6v6l4 2"/></svg>Mon – Fri: 7:30am – 4:30pm</li>
      </ul>
    </div>

    <div class="foot-rule abs"></div>
    <p class="copyright abs">© 2024 Brightline Coatings Co. All Rights Reserved.</p>
    <div class="legal abs"><span>Privacy Policy</span><i></i><span>Terms &amp; Conditions</span></div>
    <div class="to-top abs"><svg width="12" height="14" viewBox="0 0 12 14"><path d="M6 13V2M2 6l4-4 4 4" stroke="#fff" stroke-width="1.5" fill="none"/></svg></div>
  </footer>

</div>
</body>
</html>
```